Webdesign Metall- und Stahlbau Verhoelt GmbH
Zielgruppe
Metall- und Stahlbau Verhoelt GmbH
Zielgruppe: öffentlicher Bereich, Industrie, Gesundheitswesen > deutschlandweit tätig
Aufgabenstellung
keine bewegten Bilder oder Elemente in der Website
klassisches Layout
sehr konservativ

```html
<!DOCTYPE html>
<html lang="de">
<head>
<meta charset="utf-8">
<title>Metall- und Stahlbau Verhoelt GmbH</title>
<link href="https://fonts.googleapis.com/css2?family=Tinos:wght@400;700&display=swap" rel="stylesheet">
<style>
:root{
  --navy:#1d3a5f;
  --navy-dark:#173252;
  --page:#ebebeb;
  --white:#ffffff;
  --ink:#1f2a36;
  --text:#2f3338;
  --muted:#5d6670;
  --rule:#c9cbce;
  --hall-dark:#2e2a27;
  --hall-light:#6f6a63;
}
*{box-sizing:border-box;margin:0;padding:0}
html,body{width:1200px;height:1200px;overflow:hidden}
body{background:var(--page);font-family:"Tinos","Times New Roman",serif;color:var(--text);position:relative}
.site-header{position:absolute;left:0;top:0;width:1200px;height:110px;background:var(--white)}
.utility-link{position:absolute;right:220px;top:15px;font-size:12px;color:var(--ink)}
.brand{position:absolute;left:215px;top:50px;font-size:25px;color:var(--navy);display:flex;align-items:center;gap:18px}
.brand-mark{width:26px;height:18px;background:var(--navy);display:inline-block}
.main-nav{position:absolute;left:0;top:110px;width:1200px;height:54px;background:var(--navy)}
.main-nav ul{list-style:none;display:flex;gap:28px;position:absolute;left:216px;top:17px}
.main-nav li{color:var(--white);font-size:16px;position:relative}
.main-nav li.active::after{content:"";position:absolute;left:-6px;right:-8px;top:33px;height:3px;background:var(--white)}
.nav-shadow{position:absolute;left:0;top:172px;width:1200px;height:2px;background:var(--rule)}
.hero{position:absolute;left:207px;top:200px;width:774px;height:446px;background:linear-gradient(160deg,var(--hall-light) 0%,#4a4540 40%,var(--hall-dark) 100%)}
.hero-text{position:absolute;left:31px;top:306px;color:var(--white)}
.hero-text h1{font-size:44px;font-weight:700;line-height:1}
.hero-text h2{font-size:36px;font-weight:700;line-height:1.15;margin-top:6px}
.hero-text p{font-size:18px;margin-top:10px}
.divider{position:absolute;left:207px;top:695px;width:774px;height:1px;background:var(--rule)}
.section-title{position:absolute;font-size:19px;font-weight:700;color:var(--navy)}
.competences{position:absolute;left:224px;top:763px;list-style:none}
.competences li{display:flex;align-items:center;gap:14px;font-size:17px;color:var(--ink);height:27px}
.competences svg{width:20px;height:20px}
.project{position:absolute;top:752px}
.project .thumb{height:94px}
.project span{display:block;font-size:15px;color:var(--ink);margin-top:6px}
.about-text{position:absolute;left:221px;top:951px;width:270px;font-size:14.5px;line-height:18px;color:var(--ink)}
.portrait{position:absolute;left:511px;top:949px;width:125px;height:106px;background:linear-gradient(180deg,#8a8a8a,#3b3b3b)}
.certs{position:absolute;right:219px;top:902px;text-align:right}
.certs h3{font-size:19px;font-weight:700;color:var(--navy)}
.certs .phone{font-size:13px;color:var(--ink);margin-top:7px}
.certs .mail{font-size:13px;color:var(--navy);text-decoration:underline;margin-top:3px}
.download-btn{display:inline-block;margin-top:10px;background:var(--navy);color:var(--white);font-size:15px;padding:6px 15px}
.badges{display:flex;justify-content:flex-end;gap:22px;margin-top:12px}
.badge{width:30px;height:30px;border-radius:50%;border:2px solid var(--navy)}
.footer-rule{position:absolute;left:0;top:1093px;width:1200px;height:2px;background:var(--rule)}
.site-footer{position:absolute;left:0;top:1103px;width:1200px;height:89px;background:var(--navy-dark);color:var(--white)}
.footer-brand{position:absolute;left:218px;top:33px;font-size:19px}
.footer-links{position:absolute;left:542px;top:36px;display:flex;gap:25px;font-size:15px}
.copyright{position:absolute;right:220px;top:36px;font-size:15px}
</style>
</head>
<body>
<header class="site-header">
  <div class="utility-link">Kontakt &amp; Anfahrt</div>
  <div class="brand">Metall- und Stahlbau Verhoelt GmbH <span class="brand-mark"></span></div>
</header>
<nav class="main-nav">
  <ul>
    <li class="active">Home</li>
    <li>Leistung</li>
    <li>Referenzen</li>
    <li>Stellenangebote</li>
    <li>Aktuelle Meldungen</li>
    <li>Download</li>
    <li>Unternehmensvorstellung</li>
  </ul>
</nav>
<div class="nav-shadow"></div>

<section class="hero" role="img" aria-label="Werkshalle mit Stahlträgern, Kran und Schweißfunken">
  <div class="hero-text">
    <h1>Tradition trifft Innovation.</h1>
    <h2>Stahlbau seit 1965</h2>
    <p>Ihr zuverlässiger Partner bundesweit</p>
  </div>
</section>

<div class="divider"></div>

<h3 class="section-title" style="left:222px;top:719px">Unsere Kompetenzen</h3>
<ul class="competences">
  <li><svg viewBox="0 0 20 20" fill="none" stroke="#1d3a5f" stroke-width="1.4"><rect x="3" y="6" width="14" height="12"/><path d="M6 6V3h8v3M6 10h2M12 10h2M6 14h2M12 14h2"/></svg>Öffentlicher Sektor</li>
  <li><svg viewBox="0 0 20 20" fill="none" stroke="#1d3a5f" stroke-width="1.4"><circle cx="10" cy="10" r="3"/><path d="M10 2v3M10 15v3M2 10h3M15 10h3M4.3 4.3l2.1 2.1M13.6 13.6l2.1 2.1M4.3 15.7l2.1-2.1M13.6 6.4l2.1-2.1"/></svg>Industrieanlagen</li>
  <li><svg viewBox="0 0 20 20" fill="none" stroke="#1d3a5f" stroke-width="1.4"><path d="M3 4h14M5 4v13M15 4v13M5 9h10M8 9v8M12 9v8"/></svg>Gesundheitseinrichtungen</li>
</ul>

<h3 class="section-title" style="left:567px;top:719px">Aktuelle Projekte</h3>
<div class="project" style="left:568px;width:180px">
  <div class="thumb" role="img" aria-label="Brücke über einem Fluss in Berlin" style="background:linear-gradient(180deg,#b9c3cc,#6b6f6a)"></div>
  <span>Brückenbau Berlin</span>
</div>
<div class="project" style="left:760px;width:173px">
  <div class="thumb" role="img" aria-label="Klinikgebäude in Dresden" style="background:linear-gradient(180deg,#c7d3de,#7c8a6e)"></div>
  <span>Klinikum Dresden</span>
</div>

<h3 class="section-title" style="left:221px;top:919px">Über Uns</h3>
<p class="about-text">Metall- und Stahlbau Verhoelt wurde 1965 gegründet und wird heute in dritter Generation geführt. Seit 1988 fertigen wir in eigener Halle Stahlkonstruktionen für Industrie und öffentliche Bauherren.</p>
<div class="portrait" role="img" aria-label="Porträt des Geschäftsführers in der Werkshalle"></div>

<aside class="certs">
  <h3>Zertifizierungen</h3>
  <div class="phone">0351 48 27 90 15</div>
  <div class="mail">info@verhoelt-stahlbau.de</div>
  <span class="download-btn">Download</span>
  <div class="badges"><span class="badge"></span><span class="badge"></span></div>
</aside>

<div class="footer-rule"></div>
<footer class="site-footer">
  <div class="footer-brand">Metall- und Stahlbau Verhoelt GmbH</div>
  <div class="footer-links"><span>Impressum</span><span>Datenschutz</span><span>BFSG</span></div>
  <div class="copyright">© 2026</div>
</footer>
</body>
</html>
```